Fernhale Business Card Design

We are looking for a fresh business card design for our new logo. We would like a business card that is unique but friendly. We are in the window coverings business offering blinds, shutters and shades for homes.

Target Market(s)

Targeting the end-consumer

Industry/Entity Type

Business

Requirements
Must have
• Must have a dedicates space for a photo of our sales person. Must contain our new logo (attached).

```html
<!DOCTYPE html>
<html lang="en">
<head>
<meta charset="utf-8">
<title>Fernhale Business Card</title>
<link rel="stylesheet" href="https://fonts.googleapis.com/css2?family=Alegreya+Sans:wght@500&family=Lato:wght@400;700&display=swap">
<style>
  :root {
    --backdrop: #2a2a2a;
    --slate: #646569;
    --ink: #5f6064;
    --paper: #ffffff;
    --leaf: #8cc63f;
  }
  html, body {
    margin: 0;
    width: 1189px;
    height: 1200px;
    overflow: hidden;
    background: var(--backdrop);
    font-family: "Lato", sans-serif;
  }
  .card {
    position: absolute;
    left: 171px;
    width: 856px;
    height: 489px;
    border-radius: 26px;
  }
  .card--front { top: 66px; background: var(--slate); }
  .card--back  { top: 625px; background: var(--paper); }

  .brand {
    position: absolute;
    display: flex;
    align-items: center;
    gap: 24px;
  }
  .brand__mark {
    width: 94px;
    height: 94px;
    box-sizing: border-box;
    border: 4px solid currentColor;
    border-radius: 10px;
  }
  .brand__name {
    font-family: "Alegreya Sans", sans-serif;
    font-weight: 500;
    font-size: 76px;
    line-height: 1;
  }
  .card--front .brand { left: 199px; top: 195px; color: var(--paper); }
  .card--back .brand  { left: 357px; top: 53px; color: var(--ink); }

  .front__web {
    position: absolute;
    left: 0; right: 0;
    top: 401px;
    text-align: center;
    color: var(--paper);
    font-size: 19px;
    letter-spacing: 0.3em;
  }

  .portrait {
    position: absolute;
    left: 39px;
    top: 49px;
    width: 184px;
    height: 191px;
    box-sizing: border-box;
    border: 4px solid var(--leaf);
    border-radius: 16px;
    background: linear-gradient(180deg, #eef0f2 0%, #e2e4e8 55%, #2e3548 100%);
  }

  .person {
    position: absolute;
    left: 43px;
    top: 296px;
  }
  .person__name {
    margin: 0;
    font-weight: 700;
    font-size: 28px;
    color: var(--ink);
    line-height: 1;
  }
  .person__role {
    margin: 2px 0 0;
    font-size: 21px;
    color: var(--leaf);
    line-height: 1;
  }
  .rule {
    position: absolute;
    left: 115px;
    width: 699px;
    top: 342px;
    height: 1px;
    background: var(--leaf);
  }

  .contacts {
    position: absolute;
    left: 41px;
    top: 374px;
    margin: 0;
    padding: 0;
    list-style: none;
    color: var(--ink);
    font-size: 22px;
  }
  .contacts li {
    display: flex;
    align-items: center;
    gap: 11px;
    height: 28.5px;
  }
  .contacts svg { width: 26px; height: 26px; flex: none; }

  .address {
    position: absolute;
    right: 42px;
    top: 406px;
    margin: 0;
    text-align: right;
    font-style: normal;
    font-size: 21px;
    line-height: 27px;
    color: var(--ink);
  }
</style>
</head>
<body>
  <section class="card card--front">
    <div class="brand">
      <span class="brand__mark"></span>
      <span class="brand__name">Fernhale</span>
    </div>
    <p class="front__web">www.fernhaleblinds.com</p>
  </section>

  <section class="card card--back">
    <div class="portrait" role="img" aria-label="Portrait photo of the sales person"></div>

    <div class="brand">
      <span class="brand__mark"></span>
      <span class="brand__name">Fernhale</span>
    </div>

    <div class="person">
      <p class="person__name">Owen Hartley</p>
      <p class="person__role">Owner</p>
    </div>
    <div class="rule"></div>

    <ul class="contacts">
      <li>
        <svg viewBox="0 0 26 26" fill="none" stroke="#8cc63f" stroke-width="1.6">
          <circle cx="13" cy="13" r="11.5"/>
          <rect x="9.5" y="6.5" width="7" height="13" rx="1.2"/>
          <line x1="12" y1="17.3" x2="14" y2="17.3"/>
        </svg>
        (555) 014-2368
      </li>
      <li>
        <svg viewBox="0 0 26 26" fill="none" stroke="#8cc63f" stroke-width="1.6">
          <circle cx="13" cy="13" r="11.5"/>
          <rect x="7" y="9" width="12" height="8.5" rx="0.8"/>
          <path d="M7 9l6 5 6-5M7 17.5l4.5-4M19 17.5l-4.5-4"/>
        </svg>
        hello@fernhaleblinds.com
      </li>
      <li>
        <svg viewBox="0 0 26 26" fill="none" stroke="#8cc63f" stroke-width="1.6">
          <circle cx="13" cy="13" r="11.5"/>
          <circle cx="13" cy="13" r="6.5"/>
          <ellipse cx="13" cy="13" rx="3" ry="6.5"/>
          <line x1="6.5" y1="13" x2="19.5" y2="13"/>
        </svg>
        www.fernhaleblinds.com
      </li>
    </ul>

    <address class="address">PO BOX 418 Linden Road<br>3rd street Geelong</address>
  </section>
</body>
</html>
```